The book will contain the papers written by presenters at the Fresh Horizons in Beyond Contact conference held by the Institute for Luminous and Awareness Research. There will be something like 19 chapters, each about a different method people are using today to have afterlife communication with loved ones on the other side. The cover must be upbeat, inspiring, full of joy and life. Nothing with ghosts or cemeteries or skeletons or hauntings. It's about family members communicating with loved ones who are alive and well, just living on a different plane. Any image of uniting, love, and togetherness is a plus. The author name is Institute for Luminous and Awareness Research.

Industry/Entity Type

Communication

```html
<!DOCTYPE html>
<html lang="en">
<head>
<meta charset="utf-8">
<title>Fresh Horizons in Beyond Contact — Book Cover</title>
<link rel="stylesheet" href="https://fonts.googleapis.com/css2?family=Bebas+Neue&family=Crimson+Text:wght@400&display=swap">
<style>
  :root {
    --backdrop: #433f3f;
    --cover-top: #08080a;
    --cover-mid: #3c3c42;
    --cover-low: #0e0e10;
    --glow: #d9d7dc;
    --glow-soft: #8f8d94;
    --skin-light: #f0bfae;
    --skin-mid: #c98b78;
    --skin-deep: #5e3a32;
    --shadow: #0b0b0c;
    --ink-white: #ffffff;
    --ink-soft: #f0f0f0;
    --mark-blue: #2f5fb0;
  }
  * { margin: 0; padding: 0; box-sizing: border-box; }
  html, body {
    width: 1051px;
    height: 1200px;
    overflow: hidden;
    background: var(--backdrop);
  }
  .canvas {
    position: relative;
    width: 1051px;
    height: 1200px;
    display: flex;
    align-items: center;
    justify-content: center;
  }
  .book-cover {
    position: relative;
    width: 622px;
    height: 1140px;
    overflow: hidden;
    background: linear-gradient(180deg,
      var(--cover-top) 0%,
      #18181b 25%,
      var(--cover-mid) 45%,
      var(--cover-low) 100%);
  }
  .cover-artwork {
    position: absolute;
    top: 360px;
    left: 0;
    width: 622px;
    height: 780px;
    background:
      linear-gradient(180deg,
        rgba(24,24,27,1) 0%,
        rgba(24,24,27,0) 14%,
        rgba(24,24,27,0) 62%,
        rgba(11,11,12,0.85) 86%,
        rgba(11,11,12,1) 100%),
      radial-gradient(ellipse 26% 30% at 50% 36%,
        rgba(255,255,255,0.75) 0%,
        rgba(217,215,220,0.35) 55%,
        rgba(217,215,220,0) 100%),
      linear-gradient(90deg,
        var(--shadow) 0%,
        var(--skin-deep) 10%,
        var(--skin-mid) 20%,
        var(--skin-light) 27%,
        var(--glow-soft) 40%,
        var(--glow) 50%,
        var(--glow-soft) 60%,
        var(--skin-light) 73%,
        var(--skin-mid) 80%,
        var(--skin-deep) 90%,
        var(--shadow) 100%);
  }
  .cover-title {
    position: absolute;
    top: 70px;
    left: 0;
    right: 0;
    text-align: center;
    font-family: "Bebas Neue", "Oswald", sans-serif;
    color: var(--ink-white);
    font-size: 64px;
    line-height: 0.97;
    letter-spacing: 5px;
    font-weight: 400;
  }
  .cover-title span { display: block; }
  .cover-title .title-mid { letter-spacing: 11px; }
  .cover-subtitle {
    position: absolute;
    top: 288px;
    left: 40px;
    right: 40px;
    text-align: center;
    font-family: "Crimson Text", "Times New Roman", serif;
    color: var(--ink-soft);
    font-size: 17.5px;
    line-height: 1.22;
    text-transform: uppercase;
    letter-spacing: 0.3px;
  }
  .cover-subtitle span { display: block; white-space: nowrap; }
  .publisher-mark {
    position: absolute;
    bottom: 100px;
    left: 0;
    right: 0;
    display: flex;
    align-items: center;
    justify-content: center;
    gap: 10px;
  }
  .publisher-mark .mark-dot {
    width: 24px;
    height: 24px;
    border-radius: 50%;
    background: var(--mark-blue);
  }
  .publisher-mark .mark-name {
    font-family: "Crimson Text", "Times New Roman", serif;
    font-size: 34px;
    line-height: 1;
    color: var(--ink-white);
    letter-spacing: 2px;
  }
  .publisher-name {
    position: absolute;
    bottom: 56px;
    left: 0;
    right: 0;
    text-align: center;
    font-family: "Crimson Text", "Times New Roman", serif;
    font-size: 18px;
    color: var(--ink-white);
    text-transform: uppercase;
    letter-spacing: 0.2px;
    white-space: nowrap;
  }
</style>
</head>
<body>
  <main class="canvas">
    <article class="book-cover">
      <div class="cover-artwork" role="img" aria-label="Two warmly lit cupped hands gently holding a white paper-cut family of two parents and two children joined hand in hand, glowing with light in the centre"></div>
      <h1 class="cover-title">
        <span class="title-top">Fresh Horizons</span>
        <span class="title-mid">in Beyond</span>
        <span class="title-bottom">Contact</span>
      </h1>
      <p class="cover-subtitle">
        <span>19 chapters, each about a different method people</span>
        <span>are using today to have afterlife communication</span>
        <span>with loved ones on the other side</span>
      </p>
      <div class="publisher-mark">
        <span class="mark-dot"></span>
        <span class="mark-name">ILAR</span>
      </div>
      <p class="publisher-name">Institute for Luminous and Awareness Research</p>
    </article>
  </main>
</body>
</html>
```